Summit Bodyform Gym Website

We need a website design for our gym.

Summit is the UAE's first calisthenics and parkour gym. The theme under which the gym revolves is that one does not require any machinery to workout as our bodies could be themselves the machinery. The gym is designed to be the more of a social hub rather than an "in-and-out" gym, where people come train, have fun, hang out and socialize for a few hours rather than just train for 60 minutes then leave. The gym is designed to be a big open space with lots of natural sunlight, natural wood and plants all over the place to create a natural and refreshing setting. We also use recycled material throughout the gym and recycle our waste as being green is part of our philosophy. We currently also have some of the world's top and most recognized calisthenics athletes working with us.

We would like our website to reflect all that as well as provide a simple, interactive and fun way for visitors to be able to get class and gym information, check out gym media and contact us for bookings.

Target Market(s)

Ages 15-35

Industry/Entity Type

Fitness

Coding

Coded - Design and coding required

Number of Pages Required

4 page

Font styles to use
Decorative

Colors
0792cd

Requirements
Must have
• Class descriptions
• Gym description
• Class schedules
• Trainer profiles
• Gym philosophy
• Contact Details
Nice to have
• A link to contact us directly for a free first trial class

```html
<!DOCTYPE html>
<html lang="en">
<head>
<meta charset="utf-8">
<title>Summit Bodyform Gym – Contact</title>
<link rel="stylesheet" href="https://fonts.googleapis.com/css2?family=Cabin:wght@400;500;600;700&display=swap">
<style>
  :root{
    --brand:#0792cd;
    --top-strip:#d4d4d2;
    --header:#e2e4df;
    --body:#c6c6c6;
    --ink:#1e1e1e;
    --muted:#7a7a7a;
    --field:#ffffff;
    --placeholder:#b9b9b9;
    --map-land:#7d7d7d;
    --map-water:#a8cce4;
    --social:#7b7b7b;
  }
  *{box-sizing:border-box;margin:0;padding:0}
  html,body{width:1200px;height:720px;overflow:hidden}
  body{position:relative;background:var(--body);font-family:'Cabin',sans-serif;color:var(--ink)}
  .top-strip{position:absolute;left:0;top:0;width:1200px;height:23px;background:var(--top-strip)}
  .site-header{position:absolute;left:0;top:23px;width:1200px;height:61px;background:var(--header);border-bottom:1px solid #3a3a3a}
  .brand-name{position:absolute;left:350px;top:12px;font-size:30px;font-weight:600;line-height:36px;color:var(--ink)}
  .main-nav{position:absolute;left:581px;top:37px;display:flex;gap:12px;font-size:12px;line-height:16px}
  .main-nav a{color:var(--ink);text-decoration:none}
  .main-nav a.current{color:var(--muted)}
  .gym-details{position:absolute;left:310px;top:162px;width:200px}
  .gym-details h1{font-size:12px;font-weight:400;margin-bottom:14px}
  .gym-details p{font-size:8.2px;line-height:1.32;margin-bottom:6px}
  .gym-details .italic{font-style:italic}
  .gym-about{position:absolute;left:595px;top:197px;width:279px;font-size:8.6px;line-height:1.26;text-align:justify}
  .contact-title{position:absolute;left:310px;top:272px;font-size:11px;color:#fff;font-weight:500}
  .field{position:absolute;background:var(--field);color:var(--placeholder);font-size:9px;padding:10px 9px}
  .field-name{left:310px;top:291px;width:185px;height:30px}
  .field-email{left:310px;top:335px;width:185px;height:30px}
  .field-message{left:512px;top:291px;width:362px;height:75px}
  .submit{position:absolute;left:310px;top:371px;width:66px;height:24px;background:var(--brand);color:#fff;font-size:12px;font-weight:500;display:flex;align-items:center;justify-content:center}
  .map{position:absolute;left:0;top:404px;width:1200px;height:200px;background:linear-gradient(90deg,var(--map-water) 0%,var(--map-water) 18%,var(--map-land) 30%,var(--map-land) 100%)}
  .site-footer{position:absolute;left:0;top:604px;width:1200px;height:116px;background:var(--brand);border-top:3px solid #5a6a72}
  .social{position:absolute;left:509px;top:18px;display:flex;gap:10px}
  .social span{width:31px;height:31px;border-radius:50%;background:var(--social);border:2px solid #5d5d5d}
  .footer-nav{position:absolute;left:483px;top:66px;display:flex;gap:25px;font-size:7.5px;font-weight:600;color:#fff}
  .footer-nav .current{color:#5a7f98;font-weight:400}
  .footer-contacts{position:absolute;left:413px;top:90px;display:flex;align-items:center;gap:28px;font-size:9.5px;color:#fff}
  .footer-contacts .item{display:flex;align-items:center;gap:6px}
  .copyright{position:absolute;left:876px;top:96px;font-size:7.5px;color:#fff}
</style>
</head>
<body>
  <div class="top-strip"></div>
  <header class="site-header">
    <span class="brand-name">Summit</span>
    <nav class="main-nav">
      <a href="#">Gym Info</a><a href="#">Class Schedules</a><a href="#">Trainer Profiles</a><a class="current" href="#">Contact</a>
    </nav>
  </header>

  <section class="gym-details">
    <h1>Summit Gym</h1>
    <p>48 Cedar Works Road Ridgefield Industrial 2, Dubai<br>United Arab Emirates</p>
    <p>Contact: <span class="italic">+971400000000</span><br>Open hours: 7:00AM - 9:00PM</p>
    <p class="italic">email: info@summitgym.com</p>
  </section>

  <p class="gym-about">Summit is the UAE's first calisthenics and parkour gym. The theme under which the gym revolves is that one does not require any machinery to workout as our bodies could be themselves the machinery. The gym is designed to be the more of a social hub rather than an "in-and-out" gym, where people come train, have fun, hang out and socialize for a few hours rather than just train for 60 minutes then leave. The gym is designed to be a big open space with lots of natural sunlight, natural wood and plants all over the place to create a natural and refreshing setting.</p>

  <h2 class="contact-title">Contact Us</h2>
  <div class="field field-name">Enter Name</div>
  <div class="field field-email">Enter Email</div>
  <div class="field field-message">Enter Your Message</div>
  <div class="submit">Submit</div>

  <div class="map" role="img" aria-label="Street map showing the gym location in the industrial district"></div>

  <footer class="site-footer">
    <div class="social"><span></span><span></span><span></span><span></span><span></span></div>
    <nav class="footer-nav"><span>Gym Info</span><span>Class Schedules</span><span>Trainer Profiles</span><span class="current">Contact</span></nav>
    <div class="footer-contacts">
      <div class="item">
        <svg width="15" height="14" viewBox="0 0 15 14"><path d="M7.5 1 L14 7 H12 V13 H9 V9 H6 V13 H3 V7 H1 Z" fill="#fff"/></svg>
        <span>tel: +971400000000</span>
      </div>
      <div class="item">
        <svg width="10" height="15" viewBox="0 0 10 15"><path d="M5 0 C2.2 0 0 2.2 0 5 C0 8.5 5 15 5 15 C5 15 10 8.5 10 5 C10 2.2 7.8 0 5 0 Z" fill="#fff"/><circle cx="5" cy="5" r="1.8" fill="#0792cd"/></svg>
        <span>48 Cedar Works Road</span>
      </div>
      <div class="item">
        <svg width="16" height="11" viewBox="0 0 16 11"><rect x="0.5" y="0.5" width="15" height="10" fill="none" stroke="#fff"/><path d="M0.5 0.5 L8 6 L15.5 0.5" fill="none" stroke="#fff"/></svg>
        <span>info@summitgym.com</span>
      </div>
    </div>
    <div class="copyright">Summit gym 2016</div>
  </footer>
</body>
</html>
```